Brivolt Technologies business card design

We need a business card designed with our new logo. it would be great if the card could communicate it is a technology based company.

Target Market(s)

system integrators

Industry/Entity Type

technology, IOT

Contact Information for Business Card

Name, designation, Address, telephone number, email address

Requirements
Must have
• logo and company name
Nice to have
• something to do with technology

```html
<!DOCTYPE html>
<html lang="en">
<head>
<meta charset="utf-8">
<title>Brivolt Technologies – Business Card</title>
<link href="https://fonts.googleapis.com/css2?family=Saira:wght@400;600&display=swap" rel="stylesheet">
<style>
  :root {
    --backdrop: #8f8f8f;
    --card: #222222;
    --orange: #f7941d;
    --white: #ffffff;
    --muted: #e6e6e6;
  }
  * { margin: 0; padding: 0; box-sizing: border-box; }
  html, body {
    width: 1200px; height: 661px; overflow: hidden;
    background: var(--backdrop);
    font-family: "Saira", sans-serif;
  }
  .card {
    position: absolute;
    top: 193px;
    width: 480px; height: 275px;
    background: var(--card);
    overflow: hidden;
    box-shadow: 2px 3px 4px rgba(0,0,0,0.25);
  }
  .card--front { left: 107px; }
  .card--back { left: 613px; }

  .connector-lines { position: absolute; left: 0; top: 0; }

  .holder-name {
    position: absolute; left: 54px; top: 143px;
    color: var(--white);
    font-weight: 600; font-size: 25px; letter-spacing: 0.5px;
    line-height: 1;
  }
  .holder-role {
    position: absolute; left: 54px; top: 168px;
    color: var(--orange);
    font-size: 14px; line-height: 1; letter-spacing: 0.3px;
  }
  .contact-list { position: absolute; left: 54px; top: 197px; list-style: none; }
  .contact-item {
    display: flex; align-items: center; gap: 8px;
    height: 17px;
    color: var(--muted);
    font-size: 12.5px; letter-spacing: 0.3px;
  }
  .contact-icon { width: 10px; height: 10px; flex: none; }

  .front-brand {
    position: absolute; right: 22px; top: 34px;
    display: flex; flex-direction: column; align-items: flex-end; gap: 14px;
  }
  .front-brand-mark { width: 72px; height: 72px; background: var(--orange); }
  .front-brand-name {
    color: var(--white);
    font-weight: 600; font-size: 26px; line-height: 1.1;
    letter-spacing: 1px; text-transform: uppercase; text-align: right;
  }

  .brand {
    position: absolute; left: 112px; top: 173px;
    display: flex; align-items: center; gap: 10px;
  }
  .brand-mark { width: 14px; height: 14px; background: var(--orange); flex: none; }
  .brand-name {
    color: var(--orange);
    font-weight: 600; font-size: 22px; letter-spacing: 2px;
    text-transform: uppercase; line-height: 1;
  }
</style>
</head>
<body>

<section class="card card--front" aria-label="Card front">
  <svg class="connector-lines" width="480" height="275" viewBox="0 0 480 275" aria-hidden="true">
    <g fill="none" stroke-width="1.2">
      <line x1="0" y1="157" x2="34" y2="157" stroke="var(--orange)"/>
      <line x1="0" y1="179" x2="36" y2="179" stroke="var(--white)"/>
      <g stroke="var(--white)">
        <line x1="0" y1="212" x2="29" y2="212"/>
        <line x1="0" y1="221" x2="29" y2="221"/>
        <line x1="29" y1="205" x2="29" y2="239"/>
        <line x1="29" y1="205" x2="36" y2="205"/>
        <line x1="29" y1="222" x2="36" y2="222"/>
        <line x1="29" y1="239" x2="36" y2="239"/>
      </g>
    </g>
    <g>
      <rect x="33" y="155.5" width="3" height="3" fill="var(--orange)" transform="rotate(45 34.5 157)"/>
      <rect x="35" y="177.5" width="3" height="3" fill="var(--white)" transform="rotate(45 36.5 179)"/>
      <rect x="35" y="203.5" width="3" height="3" fill="var(--white)" transform="rotate(45 36.5 205)"/>
      <rect x="35" y="220.5" width="3" height="3" fill="var(--white)" transform="rotate(45 36.5 222)"/>
      <rect x="35" y="237.5" width="3" height="3" fill="var(--white)" transform="rotate(45 36.5 239)"/>
    </g>
  </svg>

  <div class="front-brand">
    <span class="front-brand-mark" aria-hidden="true"></span>
    <span class="front-brand-name">Brivolt<br>Technologies</span>
  </div>

  <h1 class="holder-name">JOHN SMITH</h1>
  <p class="holder-role">Founder &amp; CEO</p>

  <ul class="contact-list">
    <li class="contact-item">
      <svg class="contact-icon" viewBox="0 0 10 10" aria-hidden="true"><path d="M2 0.5 L3.6 2.8 L2.7 3.8 Q4 6.3 6.2 7.3 L7.2 6.4 L9.5 8 L8.4 9.5 Q2.5 8.5 0.5 1.6 Z" fill="var(--orange)"/></svg>
      <span>(123) 456-7890</span>
    </li>
    <li class="contact-item">
      <svg class="contact-icon" viewBox="0 0 10 10" aria-hidden="true"><rect x="0.5" y="2" width="9" height="6.5" fill="var(--orange)"/><path d="M0.5 2 L5 5.6 L9.5 2" fill="none" stroke="var(--card)" stroke-width="0.9"/></svg>
      <span>john@brivolttechnologies.com</span>
    </li>
    <li class="contact-item">
      <svg class="contact-icon" viewBox="0 0 10 10" aria-hidden="true"><circle cx="5" cy="5" r="4.5" fill="var(--orange)"/><path d="M5 0.5 V9.5 M0.5 5 H9.5 M5 0.5 Q2 5 5 9.5 M5 0.5 Q8 5 5 9.5" fill="none" stroke="var(--card)" stroke-width="0.7"/></svg>
      <span>brivolttechnologies.com</span>
    </li>
  </ul>
</section>

<section class="card card--back" aria-label="Card back">
  <div class="brand">
    <span class="brand-mark" aria-hidden="true"></span>
    <span class="brand-name">Brivolt Technologies</span>
  </div>
</section>

</body>
</html>
```